Redo a PPT pres. - Real Estate in Brazil - Socially equitable investments in Social Housing

We need to redo the presentation attached. It is an institutional presentation to attract local and foreign investors to invest in Brazilian Social Housing Projects structured by our company "TLR".
A middle class of 100 million, a housing deficit of 9M, a strong political will & positive income generation trends constitute grounds for a significant demand in social housing.
This make a perfect scheme for investors to invest in Brazilian Social Housing.
"TLR", is a consulting "boutique" focused in Brazilian real estate, specialized in structuring, analyzing and originating Brazilian social housing projects.
TLR is part of the group TLB. TLB is structured to create value through each step of the residential real estate business - structuring, financing, sales, marketing and technology.
We would like to see designs that use mainly the color blue. The final design should communicate financial safety and professionalism. In order to reach our needs, the designer will need to have basic understanding of finance and investment in order to highlight the most important information.
The idea is to receive back the PPT with each page redesigned and an homogeneous identity.
To all designers,
Target Market(s)
Institutional Investors and wealthy individuals
Industry/Entity Type
Residential
Look and feel

```html
<!DOCTYPE html>
<html lang="en">
<head>
<meta charset="utf-8">
<title>TLR – Social Housing in Brazil</title>
<link rel="stylesheet" href="https://fonts.googleapis.com/css2?family=PT+Serif:wght@700&family=Carlito:wght@400;700&display=swap">
<style>
:root{
  --stage:#0a1a4a;
  --navy:#0b2468;
  --navy-deep:#07185a;
  --blue:#1f5fc8;
  --blue-bright:#2f7ee6;
  --sky:#4ea4f0;
  --pale:#eef3f9;
  --ink:#1f2a3a;
  --grey:#555e6a;
  --gold:#e2b340;
  --white:#ffffff;
}
*{box-sizing:border-box;margin:0;padding:0}
html,body{width:1200px;height:900px;overflow:hidden}
body{background:var(--stage);font-family:"Carlito",Arial,sans-serif;position:relative}
.slide{position:absolute;overflow:hidden;background:var(--pale);border:1px solid #6d86c4}
.s1{left:8px;top:10px;width:580px;height:437px}
.s2{left:600px;top:10px;width:590px;height:437px}
.s3{left:10px;top:462px;width:580px;height:436px}
.s4{left:600px;top:462px;width:590px;height:436px}
.abs{position:absolute}
.photo{position:absolute}
.footer-art{position:absolute;left:0;top:0}
.brand{position:absolute;display:flex;align-items:center;gap:6px;color:var(--white);font-family:"Carlito",Arial,sans-serif;font-weight:700;font-size:40px;line-height:1}
.brand-mark{width:14px;height:14px;background:var(--white)}
.tagline{position:absolute;font-weight:700;color:var(--sky);font-size:23px;letter-spacing:.3px}
.page-no{position:absolute;width:32px;height:32px;border-radius:50%;border:1.5px solid #8fb0e6;color:var(--white);font-size:13px;font-weight:700;display:flex;align-items:center;justify-content:center;background:var(--navy-deep)}
.header-band{position:absolute;left:0;top:0;right:0;background:linear-gradient(90deg,var(--navy-deep),var(--navy) 60%,#2a5db8)}
.serif-title{font-family:"PT Serif",Georgia,serif;font-weight:700;color:var(--white);text-transform:uppercase}
/* slide 1 */
.cover-title{position:absolute;left:250px;top:114px;width:330px;height:72px;background:linear-gradient(90deg,rgba(10,40,120,.35),rgba(8,30,100,.9));display:flex;align-items:center;justify-content:flex-end;padding-right:14px;text-align:right;font-size:19px;line-height:26px}
.cover-tag{position:absolute;left:378px;top:385px;color:var(--white);font-weight:700;font-size:15px}
/* slide 2 */
.subtitle{position:absolute;font-weight:700;color:var(--grey)}
.node{position:absolute;background:linear-gradient(#3e8ff0,#1a5fc8);border:1.5px solid #cfe2fb;border-radius:3px;color:var(--white);font-size:9.5px;font-weight:700;text-align:center;line-height:11px;display:flex;align-items:center;justify-content:center;box-shadow:0 1px 3px rgba(0,0,30,.35)}
/* slide 3 */
.agenda{position:absolute;left:22px;top:118px;list-style:none}
.agenda li{display:flex;align-items:center;height:27px;font-size:13px;color:var(--ink)}
.agenda .tick{width:14px;height:14px;margin-right:12px}
.agenda .key{color:#2d7be0;margin-right:3px}
/* slide 4 */
.badge{position:absolute;left:502px;top:6px;width:80px;height:80px;border-radius:50%;background:radial-gradient(circle at 40% 35%,#3f8ff0,#0f4fb8);border:3px solid #e6effb;color:var(--white);text-align:center;font-weight:700}
.badge .num{font-size:32px;line-height:38px;padding-top:6px}
.badge .lbl{font-size:9.5px}
.panel{position:absolute;background:var(--white);border:1px solid #c9d6e8;box-shadow:0 2px 5px rgba(0,20,70,.25)}
.panel-head{height:26px;background:linear-gradient(#2f80e6,#0f4fb8);color:var(--white);font-weight:700;font-size:14px;display:flex;align-items:center;padding-left:8px}
.panel-body{padding:5px 7px;font-size:8.6px;line-height:10.6px;color:var(--ink)}
.panel-body h4{font-size:10px;margin:3px 0 2px;color:var(--ink)}
.panel-body ul{padding-left:11px;margin-bottom:2px}
.panel-body li{margin-bottom:2px}
.panel-body p{margin-bottom:9px}
</style>
</head>
<body>

<!-- Cover -->
<section class="slide s1">
  <div class="photo" role="img" aria-label="Glass office towers in blue tones" style="left:0;top:0;width:580px;height:330px;background:linear-gradient(115deg,#0f3a8c 0%,#2f6fd0 35%,#7fb3ef 55%,#3b78d6 75%,#a9c9f2 100%)"></div>
  <svg class="footer-art" width="580" height="437" viewBox="0 0 580 437">
    <path d="M0,322 C150,365 380,330 580,262 L580,437 L0,437Z" fill="var(--navy-deep)"/>
    <path d="M0,320 C150,363 380,328 580,260" fill="none" stroke="var(--gold)" stroke-width="2.5"/>
  </svg>
  <h1 class="cover-title serif-title">High yield return for a<br>quasi sovereign risk</h1>
  <div class="brand" style="left:24px;top:370px"><span class="brand-mark"></span>TLR</div>
  <p class="cover-tag">SOCIAL HOUSING IN BRAZIL</p>
</section>

<!-- How to invest -->
<section class="slide s2">
  <div class="photo" role="img" aria-label="Faint city skyline in pale blue" style="left:0;top:0;width:590px;height:437px;background:linear-gradient(100deg,#e1eaf5 0%,#f3f7fc 45%,#dce7f4 100%)"></div>
  <div class="header-band" style="height:74px"></div>
  <div class="photo" role="img" aria-label="Glass tower detail" style="left:420px;top:0;width:170px;height:74px;background:linear-gradient(90deg,rgba(40,90,180,0),#5f93d8)"></div>
  <h1 class="serif-title abs" style="left:14px;top:24px;font-size:16.5px">How to invest in social housing in Brazil?</h1>
  <p class="subtitle" style="left:16px;top:76px;font-size:17px">A socially conscious &amp; lucrative investment</p>
  <svg class="abs" style="left:180px;top:110px" width="270" height="270" viewBox="0 0 270 270">
    <defs>
      <radialGradient id="ring" cx="50%" cy="45%" r="55%">
        <stop offset="0" stop-color="#6fb1f5"/><stop offset=".7" stop-color="#2d7be0"/><stop offset="1" stop-color="#0d4db5"/>
      </radialGradient>
    </defs>
    <circle cx="135" cy="135" r="128" fill="url(#ring)"/>
    <circle cx="135" cy="135" r="62" fill="#b8bec6"/>
    <circle cx="135" cy="135" r="54" fill="#050608"/>
  </svg>
  <div class="brand" style="left:290px;top:232px;font-size:22px;gap:4px"><span class="brand-mark" style="width:8px;height:8px"></span>TLR</div>
  <div class="node" style="left:268px;top:112px;width:124px;height:30px">Building housing units for<br>low to middle-class buyers</div>
  <div class="node" style="left:375px;top:156px;width:101px;height:31px">Investing in<br>individual projects</div>
  <div class="node" style="left:403px;top:230px;width:105px;height:42px">Management<br>Specialised International<br>&amp; local team</div>
  <div class="node" style="left:375px;top:303px;width:103px;height:31px">Co-investing with local /<br>mid-size developers</div>
  <div class="node" style="left:292px;top:345px;width:78px;height:30px">Co-financed by<br>government</div>
  <div class="node" style="left:170px;top:303px;width:107px;height:31px">Equity participation of<br>R$2-10 millions</div>
  <div class="node" style="left:165px;top:230px;width:72px;height:30px">Time Horizon<br>3-4 years</div>
  <div class="node" style="left:182px;top:156px;width:70px;height:31px">Target IRR<br>25-50%</div>
  <svg class="footer-art" width="590" height="437" viewBox="0 0 590 437">
    <path d="M0,300 C170,400 400,380 590,320 L590,437 L0,437Z" fill="#2d6fd0" opacity=".5"/>
    <path d="M0,320 C170,410 400,392 590,336 L590,437 L0,437Z" fill="var(--navy-deep)"/>
  </svg>
  <div class="brand" style="left:18px;top:382px"><span class="brand-mark"></span>TLR</div>
  <div class="page-no" style="left:534px;top:358px">02</div>
  <p class="tagline" style="left:268px;top:400px">SOCIAL HOUSING IN BRAZIL</p>
</section>

<!-- Agenda -->
<section class="slide s3">
  <div class="photo" role="img" aria-label="Faint city skyline in pale blue" style="left:0;top:0;width:580px;height:436px;background:linear-gradient(100deg,#e4ecf6 0%,#f5f8fc 50%,#e0e9f5 100%)"></div>
  <div class="header-band" style="height:66px"></div>
  <div class="photo" role="img" aria-label="Glass tower detail" style="left:420px;top:0;width:160px;height:66px;background:linear-gradient(90deg,rgba(40,90,180,0),#5f93d8)"></div>
  <h1 class="serif-title abs" style="left:14px;top:24px;font-size:17px">The time is now!</h1>
  <p class="subtitle" style="left:14px;top:76px;font-size:17px">Add Sub text here</p>
  <ul class="agenda">
    <li><svg class="tick" viewBox="0 0 14 14"><path d="M1,7 L5,11 L13,2" fill="none" stroke="var(--navy)" stroke-width="2.6"/></svg><span class="key">Macro-environment &amp; Mortgage market:</span>Green Light</li>
    <li><svg class="tick" viewBox="0 0 14 14"><path d="M1,7 L5,11 L13,2" fill="none" stroke="var(--navy)" stroke-width="2.6"/></svg><span class="key">A sophisticated &amp; successful program:</span>Catalyst</li>
    <li><svg class="tick" viewBox="0 0 14 14"><path d="M1,7 L5,11 L13,2" fill="none" stroke="var(--navy)" stroke-width="2.6"/></svg><span class="key">Investment Structure of a typical project:</span>Leverage &amp; Limited Risks</li>
    <li><svg class="tick" viewBox="0 0 14 14"><path d="M1,7 L5,11 L13,2" fill="none" stroke="var(--navy)" stroke-width="2.6"/></svg><span class="key">Small &amp; mid size developers:</span>A partner by choice</li>
    <li><svg class="tick" viewBox="0 0 14 14"><path d="M1,7 L5,11 L13,2" fill="none" stroke="var(--navy)" stroke-width="2.6"/></svg><span class="key">TLR:</span>Value added &amp; Risk mitigation</li>
    <li><svg class="tick" viewBox="0 0 14 14"><path d="M1,7 L5,11 L13,2" fill="none" stroke="var(--navy)" stroke-width="2.6"/></svg><span class="key">TLB:</span>TLR, part of an integrated family of companies</li>
    <li><svg class="tick" viewBox="0 0 14 14"><path d="M1,7 L5,11 L13,2" fill="none" stroke="var(--navy)" stroke-width="2.6"/></svg><span class="key">Appendix:</span>Next step...TLR Fund (2013)</li>
  </ul>
  <svg class="footer-art" width="580" height="436" viewBox="0 0 580 436">
    <path d="M0,308 C170,400 400,380 580,318 L580,436 L0,436Z" fill="#2d6fd0" opacity=".5"/>
    <path d="M0,326 C170,412 400,394 580,336 L580,436 L0,436Z" fill="var(--navy-deep)"/>
  </svg>
  <div class="brand" style="left:16px;top:384px"><span class="brand-mark"></span>TLR</div>
  <div class="page-no" style="left:534px;top:360px">02</div>
  <p class="tagline" style="left:266px;top:398px">SOCIAL HOUSING IN BRAZIL</p>
</section>

<!-- Middle class -->
<section class="slide s4">
  <div class="photo" role="img" aria-label="Faint city skyline in pale blue" style="left:0;top:0;width:590px;height:436px;background:linear-gradient(100deg,#e6edf6 0%,#f7f9fc 50%,#e2eaf5 100%)"></div>
  <div class="photo" role="img" aria-label="Glass tower detail" style="left:400px;top:0;width:190px;height:60px;background:linear-gradient(90deg,rgba(40,90,180,0),#5f93d8)"></div>
  <h1 class="abs" style="left:14px;top:20px;font-size:18px;font-weight:700;color:var(--navy)">A MIDDLE CLASS OF 100 MILLION PEOPLE...</h1>
  <div class="badge"><div class="num">1</div><div class="lbl">GREEN LIGHT</div></div>
  <p class="subtitle" style="left:14px;top:66px;font-size:13.5px;line-height:17px;color:#4a525d">Strong political will &amp; positive income generation trends constitute grounds<br>for a significant demand in social housing</p>
  <div class="panel" style="left:12px;top:116px;width:303px;height:242px">
    <div class="panel-head">POLITICS</div>
    <div class="panel-body">
      Brazil launched a fierce battle against poverty 10 years ago with President Souza. The positive economic environment has helped implement these policies
      <h4>Growth Acceleration Program (2007-10): R$400B (*)</h4>
      <ul><li>Public investments in infrastructure</li><li>Lighten the administrative and legal burden on private initiatives and long-term growth</li><li>Stimulating Credit &amp; Financing for the real estate sector</li></ul>
      <h4>Growth Acceleration Program (2011-14): R$960B (*)</h4>
      <ul><li>« Better City » &amp; Community: R$80B</li><li>Water, Light, Transportation: R$135B</li><li>Energy: R$466B</li></ul>
      <b>Housing: R$278B</b> - public financing and subsidizes through various programs, notably <b>Casa Para Todos (CPT)</b> for low and middle classes and <b>Credito Coletivo</b>
    </div>
  </div>
  <svg class="abs" style="left:314px;top:222px" width="36" height="34" viewBox="0 0 36 34"><path d="M0,10 L20,10 L20,2 L35,17 L20,32 L20,24 L0,24Z" fill="var(--blue-bright)"/></svg>
  <div class="panel" style="left:348px;top:116px;width:232px;height:242px">
    <div class="panel-head">EMERGENCE OF THE MIDDLE CLASS</div>
    <div class="panel-body" style="font-size:9.4px;line-height:11.5px;padding-top:9px">
      <p>It reached remarkable success: poverty has decreased from 39% of population in 1999 to less than 20% in 2012</p>
      <p>More than 40M people have recently entered the middle class. They need decent housing</p>
      <p>Middle class will represent 54% of the population by the end of 2012 (overall population of 197M)</p>
      <p>Constitution of an upper middle class with an appetite for pricier products</p>
      <p>Housing deficit is estimated to be around 9M, of which 7M in urban housing</p>
    </div>
  </div>
  <svg class="footer-art" width="590" height="436" viewBox="0 0 590 436">
    <path d="M0,330 C170,405 400,388 590,330 L590,436 L0,436Z" fill="#2d6fd0" opacity=".5"/>
    <path d="M0,346 C170,418 400,402 590,346 L590,436 L0,436Z" fill="var(--navy-deep)"/>
  </svg>
  <div class="brand" style="left:18px;top:386px"><span class="brand-mark"></span>TLR</div>
  <div class="page-no" style="left:540px;top:366px">02</div>
  <p class="tagline" style="left:336px;top:404px;font-size:20px">SOCIAL HOUSING IN BRAZIL</p>
</section>

</body>
</html>
```